Pimping of pitching slides for a startup in the medical field

We have a powerpoint presentation for pitching events (for potential investors) and the slides need some improvement.
Please create:
1. A slide master - a layout template including the Meditrova logo, a title, and some empty space to be filled with pictures and/or text. This empty space needs to have a white background, as many of our illustrations have a white background and it is easier for printing later.
2. Pimp the existing slides (they are attached). You can improve all of them, but you don't have to. The following slides need to be reworked for sure however: 1, 13, 14, 15, 20, 21, 22, 23. Please use the text on the slides. However, you may change or add or remove the pictures and everything else.
If you want to use additional visual material, please feel free to do so.
You can use visual material from http://www.pixvaultimages.example/ and we will pay the royalties later. Just use the pictures with the watermarks in the meantime and let us know, which one it is. Also, try to use pictures that cost 15 credits or less.
You can also use any visual material you find on our websites and also any single illustration from our product video. Let us know if you need something.
Websites:
Company - http://www.meditrova-example.com/
Product - http://www.trackyourache.example/
Product video:
https://www.vidstreamhub.example/watch?v=Qa3pLm9xZtR
In general, the design should look modern, yet coming from a trustworthy company.
Learn more about us through the above mentioned links. The designs on the websites do however not need to be taken as a template - we want to change it eventually.
Looking forward seeing your suggestions!
Hi everyone,
http://shotgallery.example/shots/5820391-Summit-Slide-Layout/attachments/730184
http://designmarket.example/item/olu-deluxe-slide-layout/7261038?ref=tvbk5527
http://www.portfoliohive.example/gallery/Fresh-Slidedeck/36291748
http://shotgallery.example/shots/5894120-Slidedeck-layout/attachments/735512
http://www.portfoliohive.example/gallery/Venture-Deck-Slides/36804217
Medical

```html
<!DOCTYPE html>
<html lang="en">
<head>
<meta charset="utf-8">
<title>Recent data – Meditrova</title>
<link rel="stylesheet" href="https://fonts.googleapis.com/css2?family=Carlito:wght@400;700&display=swap">
<style>
  :root {
    --brand-blue: #00aeef;
    --white: #ffffff;
    --ink: #111111;
    --grid: #8c8c8c;
    --q1: #3b8499;
    --q2: #4ba3b9;
    --q3: #7fbccf;
    --q4: #b5d7e2;
    --s1: #3b8499;
    --s2: #4ba9c4;
    --s3: #a9d3e0;
    --ghost: #fbf0f1;
  }
  * { margin: 0; padding: 0; box-sizing: border-box; }
  html, body { width: 1200px; height: 863px; overflow: hidden; background: var(--white); }
  body { font-family: "Carlito", "Calibri", sans-serif; color: var(--ink); }
  .slide { position: relative; width: 1200px; height: 863px; overflow: hidden; background: var(--white); }
  .side-panel { position: absolute; inset: 0; width: 1200px; height: 863px; }
  .side-panel polygon { fill: var(--brand-blue); }
  .slide-title {
    position: absolute; left: 34px; top: 18px;
    font-size: 78px; font-weight: 400; color: var(--white);
    letter-spacing: 0.5px; line-height: 1;
  }
  .slide-intro {
    position: absolute; left: 35px; top: 121px; width: 415px;
    font-size: 19.5px; font-weight: 700; line-height: 26.5px;
    color: var(--white); letter-spacing: -0.3px;
  }
  .brand {
    position: absolute; left: 20px; top: 800px;
    display: flex; align-items: center; gap: 12px;
    color: var(--white); font-size: 36px; font-weight: 400;
  }
  .brand-dot { width: 22px; height: 22px; border-radius: 50%; background: var(--white); }
  .charts { position: absolute; inset: 0; width: 1200px; height: 863px; }
  .charts text { font-family: "Carlito", "Calibri", sans-serif; fill: var(--ink); }
  .legend-label { font-size: 15px; }
  .axis-label { font-size: 17px; }
  .ghost-word { font-size: 78px; fill: var(--ghost) !important; }
  .grid-line { stroke: var(--grid); stroke-width: 1; fill: none; }
</style>
</head>
<body>
<main class="slide">
  <svg class="side-panel" viewBox="0 0 1200 863" aria-hidden="true">
    <polygon points="0,0 370,0 537,38 460,863 0,863"/>
  </svg>

  <h1 class="slide-title">recent data</h1>
  <p class="slide-intro">Lorem ipsum dolor sit amet, consectetur adipis-ing elit.Ut sit amet leo et lacus vehicula ullam-corper in sit amet neque.Nam bibendum odio bibendum augue ultrices placerat vitae vitae tel-lus.ed ut enim dapibus, eleifend metus quis, ul-lamcorper dui.Morbi ultrices turpis eget egestas venenatis.</p>

  <div class="brand"><span class="brand-dot"></span><span class="brand-name">Meditrova</span></div>

  <svg class="charts" viewBox="0 0 1200 863" role="img" aria-label="Quarterly pie chart and stacked category column chart">
    <defs>
      <linearGradient id="grad-s1" x1="0" x2="1"><stop offset="0" stop-color="#2f6f82"/><stop offset="0.45" stop-color="#4a97ad"/><stop offset="1" stop-color="#2f6f82"/></linearGradient>
      <linearGradient id="grad-s2" x1="0" x2="1"><stop offset="0" stop-color="#3a93ad"/><stop offset="0.45" stop-color="#62bcd4"/><stop offset="1" stop-color="#3a93ad"/></linearGradient>
      <linearGradient id="grad-s3" x1="0" x2="1"><stop offset="0" stop-color="#8fc2d2"/><stop offset="0.45" stop-color="#c4e3ec"/><stop offset="1" stop-color="#8fc2d2"/></linearGradient>
    </defs>

    <!-- pie -->
    <g class="pie">
      <path fill="var(--q1)" d="M834,228 L834,110 A118,118 0 1 1 773.4,329.2 Z"/>
      <path fill="var(--q2)" d="M796,240 L735.4,341.2 A118,118 0 0 1 687.6,193.5 Z"/>
      <path fill="var(--q3)" d="M804,202 L695.6,155.5 A118,118 0 0 1 743.6,100.6 Z"/>
      <path fill="var(--q4)" d="M824.4,193.3 L764,91.9 A118,118 0 0 1 824.4,75.3 Z"/>
    </g>
    <g class="pie-legend">
      <rect x="641" y="390" width="9" height="9" fill="var(--q1)"/><text class="legend-label" x="656" y="401">1st Qtr</text>
      <rect x="732" y="390" width="9" height="9" fill="var(--q2)"/><text class="legend-label" x="747" y="401">2nd Qtr</text>
      <rect x="825" y="390" width="9" height="9" fill="var(--q3)"/><text class="legend-label" x="840" y="401">3rd Qtr</text>
      <rect x="916" y="390" width="9" height="9" fill="var(--q4)"/><text class="legend-label" x="931" y="401">4th Qtr</text>
    </g>

    <text class="ghost-word" x="573" y="512">statistics</text>

    <!-- column chart grid -->
    <g class="grid">
      <path class="grid-line" d="M627,766 L655,746 L1032,746 M627,766 L1003,766 L1032,746"/>
      <path class="grid-line" d="M627,730 L655,710 L1032,710"/>
      <path class="grid-line" d="M627,694 L655,674 L1032,674"/>
      <path class="grid-line" d="M627,659 L655,639 L1032,639"/>
      <path class="grid-line" d="M627,623 L655,603 L1032,603"/>
      <path class="grid-line" d="M627,587 L655,567 L1032,567"/>
      <path class="grid-line" d="M627,552 L655,532 L1032,532"/>
      <path class="grid-line" d="M627,516 L655,496 L1032,496"/>
      <path class="grid-line" d="M627,516 L627,766 M655,496 L655,746"/>
      <path class="grid-line" d="M720,766 v6 M814,766 v6 M908,766 v6 M1003,766 v6 M620,766 h7"/>
    </g>
    <g class="axis" text-anchor="end">
      <text class="axis-label" x="606" y="772">0</text>
      <text class="axis-label" x="606" y="736">2</text>
      <text class="axis-label" x="606" y="700">4</text>
      <text class="axis-label" x="606" y="665">6</text>
      <text class="axis-label" x="606" y="629">8</text>
      <text class="axis-label" x="606" y="593">10</text>
      <text class="axis-label" x="606" y="558">12</text>
      <text class="axis-label" x="606" y="522">14</text>
    </g>

    <!-- columns: category 1 -->
    <g class="column">
      <ellipse cx="689" cy="756" rx="20" ry="6" fill="url(#grad-s1)"/>
      <rect x="669" y="679" width="40" height="77" fill="url(#grad-s1)"/>
      <rect x="669" y="636" width="40" height="43" fill="url(#grad-s2)"/>
      <rect x="669" y="601" width="40" height="35" fill="url(#grad-s3)"/>
      <ellipse cx="689" cy="601" rx="20" ry="6" fill="#9ccbd9"/>
    </g>
    <g class="column">
      <ellipse cx="782" cy="756" rx="20" ry="6" fill="url(#grad-s1)"/>
      <rect x="762" y="711" width="40" height="45" fill="url(#grad-s1)"/>
      <rect x="762" y="633" width="40" height="78" fill="url(#grad-s2)"/>
      <rect x="762" y="597" width="40" height="36" fill="url(#grad-s3)"/>
      <ellipse cx="782" cy="597" rx="20" ry="6" fill="#9ccbd9"/>
    </g>
    <g class="column">
      <ellipse cx="876" cy="756" rx="20" ry="6" fill="url(#grad-s1)"/>
      <rect x="856" y="693" width="40" height="63" fill="url(#grad-s1)"/>
      <rect x="856" y="661" width="40" height="32" fill="url(#grad-s2)"/>
      <rect x="856" y="608" width="40" height="53" fill="url(#grad-s3)"/>
      <ellipse cx="876" cy="608" rx="20" ry="6" fill="#9ccbd9"/>
    </g>
    <g class="column">
      <ellipse cx="970" cy="756" rx="20" ry="6" fill="url(#grad-s1)"/>
      <rect x="950" y="676" width="40" height="80" fill="url(#grad-s1)"/>
      <rect x="950" y="626" width="40" height="50" fill="url(#grad-s2)"/>
      <rect x="950" y="537" width="40" height="89" fill="url(#grad-s3)"/>
      <ellipse cx="970" cy="537" rx="20" ry="6" fill="#9ccbd9"/>
    </g>

    <g class="categories" text-anchor="middle">
      <text class="axis-label" x="673" y="800">Category</text><text class="axis-label" x="673" y="825">1</text>
      <text class="axis-label" x="766" y="800">Category</text><text class="axis-label" x="766" y="825">2</text>
      <text class="axis-label" x="860" y="800">Category</text><text class="axis-label" x="860" y="825">3</text>
      <text class="axis-label" x="954" y="800">Category</text><text class="axis-label" x="954" y="825">4</text>
    </g>

    <g class="series-legend">
      <rect x="1061" y="617" width="11" height="11" fill="var(--s3)"/><text class="axis-label" x="1078" y="629">Series 3</text>
      <rect x="1061" y="649" width="11" height="11" fill="var(--s2)"/><text class="axis-label" x="1078" y="661">Series 2</text>
      <rect x="1061" y="681" width="11" height="11" fill="var(--s1)"/><text class="axis-label" x="1078" y="693">Series 1</text>
    </g>
  </svg>
</main>
</body>
</html>
```